Lurvik.no is a new website about pedagogical entrepreneurship. It's main target group is teachers. The Nordic Bureau for Digital Schooling and the National Office for Learning and Classrooms are leading the project.

The web page is meant to show examples of how different methods of entrepreneurship can be used pedagogical in a learning environment. The page will also support the user with examples of different teaching programs and other examples of best practice.

Pedagogical entrepreneurship is not about business and men in suits. It's a method for learning. The focus in the design should be on school, education and new ways of learning.

The final product should be motivating and engaging, but at the same time governmental and serious. We are not looking for something "flashy" and corporate-looking, but a moderate, task-focused and clean design that state quality.

We need designs for three pages:
1 - frontpage
2 - subpage ("Metoder og undervisningsopplegg")
3 - subpage ("Små-TOPP i Vassbygd")

The interaction design for these three pages will be uploaded as an attachment.

We would like you to find inspiration in the following websites:
- www.skapekraft.no
- www.giellu.no
- www.brightfernlab.com
- www.zyx.no
(more will be added)

Please use the attached logo, and feel free to use this as an inspiration for the rest of the design.

Target Market(s)

Teachers

Industry/Entity Type

Education

Requirements
Must have
• * Header with: Logo. Main navigation. Utility navigation. Search box.
* Footer
Should not have
• Images of men in suits.
Very strong graphical elements that stands out too much (we want it clean).

```html
<!DOCTYPE html>
<html lang="en">
<head>
<meta charset="utf-8">
<title>Lurvik.no – Good examples, best practice</title>
<link href="https://fonts.googleapis.com/css2?family=Ubuntu:wght@300;400;500;700&family=Arimo:wght@400;700&display=swap" rel="stylesheet">
<style>
:root{
  --navy:#1b4d86;
  --blue:#1e6fb3;
  --sky:#33a6e3;
  --pale:#cfe6f6;
  --green:#35b53c;
  --ink:#222;
  --footer:#1d4e85;
  --footer-deep:#17406f;
  --link-light:#5ab4ec;
}
*{margin:0;padding:0;box-sizing:border-box}
html,body{width:965px;height:1200px;overflow:hidden;background:#fff}
.page{position:relative;width:1200px;height:1493px;transform:scale(.80417);transform-origin:0 0;
  font-family:Arimo,Arial,sans-serif;color:var(--ink);
  background:linear-gradient(#fff 0,#fff 1140px,#cfe5f6 1180px,#5b9fd6 1225px,var(--footer) 1235px)}
.abs{position:absolute}
.topline{left:0;top:0;width:1200px;height:10px;background:linear-gradient(90deg,#1e5c9d,#6fc0ee 50%,#1e5c9d)}
.utility{left:541px;top:17px;display:flex;gap:30px;font-size:11px;font-weight:700;color:var(--navy)}
.search{left:900px;top:10px;width:150px;height:27px;background:var(--blue);border-radius:0 0 4px 4px;color:#a9d3f0;font-size:11px;padding:7px 10px}
.search svg{position:absolute;right:10px;top:4px}
.brand{left:140px;top:48px;display:flex;align-items:center;gap:22px}
.brand-dot{width:62px;height:62px;border-radius:50%;background:var(--blue)}
.brand-name{font-family:Ubuntu,sans-serif;font-weight:500;font-size:46px;color:var(--blue);line-height:1}
.brand-tag{font-size:10px;color:var(--navy);margin-top:3px}
.mainnav{left:536px;top:56px;display:flex}
.mainnav .item{display:flex;align-items:center;gap:6px;font-family:Ubuntu,sans-serif;font-size:14px;line-height:17px;padding:0 18px 0 0;height:48px}
.mainnav .sep{width:1px;height:40px;border-left:1px dashed #9ccbe9;margin:4px 18px 0 0}
.nav-what{color:var(--blue)}
.nav-methods,.nav-good{color:var(--green)}
.nav-good{border-bottom:3px solid var(--green);padding-right:0!important}
.section-title{left:162px;top:145px;display:flex;align-items:flex-end}
.section-title h1{font-family:Ubuntu,sans-serif;font-weight:400;font-size:19px;color:var(--blue);margin-left:4px;white-space:nowrap}
.section-rule{left:476px;top:179px;width:574px;height:4px;background:#6fbbe8}
.crumb{left:197px;top:192px;font-size:11px;font-weight:700;color:var(--blue)}
.feature{left:158px;top:218px;width:892px;height:308px;border:1px solid #7cc2ec;border-top-color:transparent;border-radius:0 0 6px 6px;background:#fff}
.feature-shadow{left:175px;top:526px;width:860px;height:22px;background:radial-gradient(ellipse at top,rgba(120,150,180,.35),transparent 70%)}
.photo{border:1px solid #7cc2ec}
.feature .photo{left:34px;top:16px;width:358px;height:246px;background:linear-gradient(135deg,#a8b7c3,#d8c6b6 55%,#8e8f9b)}
.feature h2{left:418px;top:12px;font-family:Ubuntu,sans-serif;font-weight:300;font-size:28px;color:var(--navy)}
.lead{left:418px;top:50px;width:420px;font-size:11px;font-weight:700;color:var(--navy);line-height:17px}
.body-copy{left:418px;top:97px;width:430px;font-size:11px;line-height:17px}
.facts{left:0;top:178px;width:890px;height:35px;background:var(--sky)}
.facts .row{position:absolute;left:422px;top:6px;display:flex;gap:34px;color:#fff;font-size:11px;font-weight:700;align-items:center}
.facts span{display:flex;align-items:center;gap:5px}
.meta{left:420px;top:230px;display:flex;gap:30px}
.meta div{display:flex;gap:8px;align-items:center}
.meta b{display:block;color:var(--blue);font-size:13px}
.meta i{font-style:normal;color:var(--sky);font-size:13px}
.panel{border:1px solid #d0d0d0;border-top:none;border-radius:0 0 6px 6px;background:linear-gradient(160deg,#fff 70%,#eaeaea)}
.panel-head{position:absolute;left:-1px;top:0;right:-1px;height:32px;border-radius:5px 5px 0 0;background:linear-gradient(#3a7cbd,#1c5390);color:#fff;font-family:Ubuntu,sans-serif;font-weight:300;font-size:20px;padding:3px 18px}
.howto{left:158px;top:559px;width:586px;height:325px}
.howto .text{position:absolute;left:20px;top:44px;width:530px;font-size:11px;line-height:17px}
.howto h3{font-size:13px;font-weight:700;letter-spacing:.5px;color:var(--blue);margin-top:12px}
.howto h3:first-child{margin-top:0}
.media{left:767px;top:559px;width:283px;height:325px}
.tabs{left:8px;top:38px;display:flex;font-family:Ubuntu,sans-serif;font-size:17px}
.tabs span{padding:3px 10px;color:var(--blue)}
.tabs .on{background:var(--sky);color:#fff}
.media-box{left:1px;top:65px;width:279px;height:221px;background:var(--sky)}
.video{left:10px;top:13px;width:258px;height:162px;background:linear-gradient(#4a5f6e,#a89c86 55%,#3b3b3b);border:2px solid #222}
.video-bar{left:0;bottom:0;width:100%;height:12px;background:#111}
.caption{left:12px;top:185px;width:250px;font-size:10px;color:#e6f4fc;line-height:14px}
.more-btn{left:125px;top:293px;width:148px;height:24px;border-radius:4px;background:linear-gradient(#55b6ea,#1e7dc2);color:#fff;font-family:Ubuntu,sans-serif;font-weight:500;font-size:12px;padding:5px 9px}
.more-btn svg{position:absolute;right:-2px;top:-3px}
.related{left:160px;top:913px;width:890px;height:230px}
.card{top:44px;width:280px;height:140px}
.card .photo{left:0;top:0;width:137px;height:137px;border:none;box-shadow:0 3px 6px rgba(0,0,0,.25)}
.card h4{left:147px;top:0;width:130px;font-family:Arimo,Arial,sans-serif;font-weight:400;font-size:14px;line-height:18px;color:#222}
.card p{left:147px;top:40px;width:128px;font-size:10.5px;line-height:13.6px}
.card a{left:147px;top:116px;font-size:11px;color:#222;text-decoration:none}
.arrow{top:1009px;width:19px;height:48px;display:flex;align-items:center;justify-content:center}
.arrow.prev{left:142px;background:var(--navy)}
.arrow.next{left:1051px;background:#2fb7d9}
.dots{left:563px;top:1116px;display:flex;gap:6px}
.dots i{width:15px;height:15px;border:2px solid var(--blue);border-radius:50%}
.dots i.on{background:var(--sky)}
.footer-rule{left:0;top:1314px;width:1200px;height:2px;background:#3378ba}
.footer-top-band{left:0;top:1226px;width:1200px;height:8px;background:linear-gradient(90deg,transparent,#8bc7ef 30%,transparent 50%)}
.foot-brand{left:160px;top:1260px;display:flex;align-items:center;gap:14px}
.foot-brand .brand-dot{width:46px;height:46px;background:#e8f3fb}
.foot-brand .brand-name{font-size:36px;color:#7cc3f0}
.foot-brand .brand-tag{font-size:8px;color:#a8cfee}
.foot-col{color:#fff}
.foot-col h5{font-family:Ubuntu,sans-serif;font-weight:400;font-size:19px;line-height:22px;display:flex;align-items:center;gap:8px;height:50px}
.foot-col ul{list-style:none;margin-top:14px;font-size:11px;color:#d8e8f6}
.foot-col li{height:22.5px}
.foot-col li.cur{color:var(--link-light)}
.copyright{left:170px;top:1325px;font-size:11px;color:var(--link-light)}
</style>
</head>
<body>
<div class="page">
  <div class="abs topline"></div>

  <nav class="abs utility"><span>Best practice shools</span><span>Lurvikmeter</span><span>About lurvik.no</span></nav>
  <div class="abs search">Searching for...
    <svg width="22" height="20" viewBox="0 0 22 20"><circle cx="8" cy="8" r="5.5" fill="none" stroke="#d9ecf9" stroke-width="2"/><path d="M12 12l7 6" stroke="#d9ecf9" stroke-width="3"/></svg>
  </div>

  <div class="abs brand">
    <div class="brand-dot"></div>
    <div><div class="brand-name">Lurvik</div><div class="brand-tag">Entreprenørielle metoder i undervisningen</div></div>
  </div>

  <nav class="abs mainnav">
    <div class="item nav-what">
      <svg width="44" height="44" viewBox="0 0 44 44"><circle cx="26" cy="18" r="13" fill="none" stroke="#1e6fb3" stroke-width="3"/><circle cx="26" cy="15" r="5" fill="#1e6fb3"/><path d="M18 30q8-10 16 0z" fill="#1e6fb3"/><path d="M15 28L4 40" stroke="#1e6fb3" stroke-width="5" stroke-linecap="round"/></svg>
      <span>What is<br>pedagogical<br>entrepreneurship?</span>
    </div>
    <div class="sep"></div>
    <div class="item nav-methods">
      <svg width="44" height="44" viewBox="0 0 44 44" fill="none" stroke="#35b53c" stroke-width="3"><circle cx="8" cy="34" r="5"/><circle cx="20" cy="22" r="5"/><circle cx="36" cy="8" r="5"/><path d="M11 30l6-5M24 19l8-7"/></svg>
      <span>Methods and<br>teaching plans</span>
    </div>
    <div class="sep"></div>
    <div class="item nav-good">
      <svg width="40" height="48" viewBox="0 0 40 48"><path d="M20 46V22" stroke="#35b53c" stroke-width="4"/><path d="M20 24Q4 22 2 8q14 0 18 16zM20 20q2-14 16-18q0 14-16 18z" fill="#35b53c"/></svg>
      <span>Good examples,<br>best practice</span>
    </div>
  </nav>

  <div class="abs section-title">
    <svg width="30" height="40" viewBox="0 0 30 40"><path d="M12 40V18" stroke="#1e6fb3" stroke-width="3"/><path d="M12 20Q2 18 1 8q10 0 11 12zM12 16q2-10 12-14q0 11-12 14z" fill="#1e6fb3"/></svg>
    <h1>GOOD EXAMPLES, BEST PRACTICE</h1>
  </div>
  <div class="abs section-rule"></div>
  <div class="abs crumb">Sub menu &nbsp;»&nbsp; Små-TOPP at Vassbygd school</div>

  <div class="abs feature-shadow"></div>
  <section class="abs feature">
    <div class="abs photo" role="img" aria-label="Photo of smiling students working together at a classroom table"></div>
    <h2 class="abs">Main title comes here</h2>
    <p class="abs lead">Lorem ipsum dolor sit amet, consectetur adipiscing elit. Praesent vestibulum iaculis convallis. Morbi sed mauris eros, a dictum risus. Nam adipiscing</p>
    <p class="abs body-copy">Phasellus ut pretium mauris. Cras non leo dui, et molestie ante. Class aptent taciti sociosqu ad litora torquent per conubia nostra, per inceptos himenaeos. Cras aliquam elit sit amet mi commodo eu varius leo commodo. Suspendisse fringilla facilisis neque. Donec egestas, dui sed mattis consectetur, diam elit feugiat est.</p>
    <div class="abs facts"><div class="row">
      <span><svg width="24" height="24" viewBox="0 0 24 24"><rect x="5" y="5" width="14" height="14" transform="rotate(45 12 12)" fill="none" stroke="#fff" stroke-width="2"/><path d="M9 13l3-3v2h4v2h-4v2z" fill="#fff"/></svg>TOPP</span>
      <span><svg width="24" height="24" viewBox="0 0 24 24" fill="none" stroke="#fff" stroke-width="2"><circle cx="12" cy="12" r="10"/><circle cx="12" cy="12" r="5"/><circle cx="12" cy="12" r="1.5" fill="#fff"/></svg>English, Norwegian, Math</span>
      <span><svg width="24" height="26" viewBox="0 0 24 26" fill="none" stroke="#fff" stroke-width="2"><circle cx="12" cy="15" r="9"/><path d="M12 15V9M9 3h6"/></svg>1 day</span>
    </div></div>
    <div class="abs meta">
      <div><svg width="36" height="34" viewBox="0 0 36 34"><path d="M3 17L18 5l15 12h-4v15H7V17z" fill="#1e6fb3"/><path d="M22 2v10M22 2h8l-2 2 2 2h-8" fill="#1e6fb3" stroke="#1e6fb3"/></svg><span><b>Title</b><i>Vassbygd skole</i></span></div>
      <div><svg width="36" height="34" viewBox="0 0 36 34"><circle cx="18" cy="10" r="8" fill="#1e6fb3"/><path d="M2 34q0-14 16-14t16 14z" fill="#1e6fb3"/></svg><span><b>Contact</b><i>John Doe</i></span></div>
    </div>
  </section>

  <section class="abs panel howto">
    <div class="panel-head">This is how we did it</div>
    <div class="text">
      <h3>Lorem ipsum</h3>
      <p>dolor sit amet, consectetur adipiscing elit. Praesent vestibulum iaculis convallis. Morbi sed mauris eros, a dictum risus. Nam adipiscing egestas arcu gravida mollis. Duis ac diam ante. Nulla at nulla est.</p>
      <h3>Phasellus ut pretium mauris.</h3>
      <p>Cras non leo dui, et molestie ante. Class aptent taciti sociosqu ad litora torquent per conubia nostra, per inceptos himenaeos. Cras aliquam elit sit amet mi commodo eu varius leo commodo. Suspendisse fringilla facilisis neque. Donec egestas, dui sed mattis consectetur, diam elit feugiat est, quis iaculis lorem nisl volutpat velit. Etiam lacinia hendrerit nisi in commodo torquent per conubia nostra, per.</p>
      <h3 style="margin-top:16px">Cras aliquam elit sit amet</h3>
      <p>mi commodo eu varius leo commodo. Suspendisse fringilla facilisis neque. Donec egestas, dui sed mattis consectetur, diam elit feugiat est, quis iaculis lorem nisl volutpat velit. Etiam lacinia hendrerit nisi in commodo. torquent per conubia nostra, per inceptos himenaeos. Cras aliquam elit sit amet mi commodo eu varius leo commodo.</p>
    </div>
  </section>

  <section class="abs panel media">
    <div class="panel-head">Multimedia</div>
    <div class="abs tabs"><span class="on">VIDEOS</span><span>PHOTOS</span></div>
    <div class="abs media-box">
      <div class="abs video" role="img" aria-label="Video still of mountains above a sea of clouds"><div class="abs video-bar"></div></div>
      <p class="abs caption">This video is about lorem ipsum dolor set imut vit husctkeliro facilis neque.</p>
    </div>
    <div class="abs more-btn">SEE MORE VIDEOS
      <svg width="30" height="30" viewBox="0 0 30 30"><rect x="5" y="5" width="20" height="20" transform="rotate(45 15 15)" fill="#fff" stroke="#1e6fb3" stroke-width="2"/><path d="M12 9l6 6-6 6" fill="none" stroke="#1e6fb3" stroke-width="3"/></svg>
    </div>
  </section>

  <section class="abs panel related">
    <div class="panel-head">You might also want to see</div>
    <article class="abs card" style="left:22px">
      <div class="abs photo" role="img" aria-label="Photo of a student carrying a stack of books in a library" style="background:linear-gradient(135deg,#e9c66a,#d9d2c4 50%,#b7a999)"></div>
      <h4 class="abs">Lorem ipsum dolor sit amet</h4>
      <p class="abs">Onsectetur adipiscing elit. Onsectetur elit dolor onsectetur adipiscing elit, sectetur adipiscing dolor elit</p>
      <a class="abs" href="#">» Read more</a>
    </article>
    <article class="abs card" style="left:318px">
      <div class="abs photo" role="img" aria-label="Photo of students writing at their desks" style="background:linear-gradient(135deg,#5b4d4a,#b9a19a 50%,#e3dcd6)"></div>
      <h4 class="abs">Lorem ipsum dolor sit amet</h4>
      <p class="abs">Onsectetur adipiscing elit. Onsectetur elit dolor onsectetur adipiscing elit, sectetur adipiscing dolor elit</p>
      <a class="abs" href="#">» Read more</a>
    </article>
    <article class="abs card" style="left:610px">
      <div class="abs photo" role="img" aria-label="Photo of a student concentrating on written work" style="background:linear-gradient(135deg,#e9e7e4,#c9a58a 50%,#f1efec)"></div>
      <h4 class="abs">Lorem ipsum dolor sit amet</h4>
      <p class="abs">Onsectetur adipiscing elit. Onsectetur elit dolor onsectetur adipiscing elit, sectetur adipiscing dolor elit</p>
      <a class="abs" href="#">» Read more</a>
    </article>
  </section>
  <div class="abs arrow prev"><svg width="10" height="14" viewBox="0 0 10 14"><path d="M8 1L2 7l6 6" fill="none" stroke="#fff" stroke-width="3"/></svg></div>
  <div class="abs arrow next"><svg width="10" height="14" viewBox="0 0 10 14"><path d="M2 1l6 6-6 6" fill="none" stroke="#fff" stroke-width="3"/></svg></div>
  <div class="abs dots"><i></i><i class="on"></i><i></i><i></i></div>

  <footer>
    <div class="abs footer-top-band"></div>
    <div class="abs foot-brand">
      <div class="brand-dot"></div>
      <div><div class="brand-name">Lurvik</div><div class="brand-tag">Entreprenørielle metoder i undervisningen</div></div>
    </div>
    <div class="abs footer-rule"></div>
    <p class="abs copyright">All rights reserved | Lurvik.no 2012</p>

    <div class="abs foot-col" style="left:410px;top:1262px">
      <h5><svg width="42" height="42" viewBox="0 0 44 44"><circle cx="26" cy="18" r="13" fill="none" stroke="#fff" stroke-width="3"/><circle cx="26" cy="15" r="5" fill="#fff"/><path d="M18 30q8-10 16 0z" fill="#fff"/><path d="M15 28L4 40" stroke="#fff" stroke-width="5" stroke-linecap="round"/></svg>Pedagogical<br>entrepreneurship</h5>
      <ul style="margin-left:49px"><li>» What is Pedagogical entrepreneurship?</li><li>» Science</li><li>» Best practice schools</li><li>» Lurvikmeter</li><li>» About lurvik.no</li></ul>
    </div>
    <div class="abs foot-col" style="left:698px;top:1262px">
      <h5><svg width="42" height="42" viewBox="0 0 44 44" fill="none" stroke="#fff" stroke-width="3"><circle cx="8" cy="34" r="5"/><circle cx="20" cy="22" r="5"/><circle cx="36" cy="8" r="5"/><path d="M11 30l6-5M24 19l8-7"/></svg>Methods</h5>
      <ul style="margin-left:46px"><li class="cur">» Story line</li><li>» Topp</li><li>» Café-pedagogikk</li><li>» Blabla</li></ul>
    </div>
    <div class="abs foot-col" style="left:886px;top:1262px">
      <h5><svg width="34" height="44" viewBox="0 0 40 48"><path d="M20 46V22" stroke="#fff" stroke-width="4"/><path d="M20 24Q4 22 2 8q14 0 18 16zM20 20q2-14 16-18q0 14-16 18z" fill="#fff"/></svg>Inspirations</h5>
      <ul style="margin-left:42px"><li>» Lorem ipsum</li><li>» Dolor sit amet</li><li>» Onsectetur</li><li>» Adipiscing elit</li></ul>
    </div>
  </footer>
</div>
</body>
</html>
```